Vernac Law Business cards and stationary design project

We are looking for a stationary design for business cards (double sided), 8x10, 5x7, and legal and standard envelopes.

We would like the design to match the logo that we have already.
Color palate preferred is Teal, White, grey and any others that will look good for a professional law firm.

We would like this statement: "RELATIONSHIPS. RESPECT. RESULT" to be on the back of the business cards and maybe on the stationary if it looks good.

Please see link to website for more information: www.vernac-law.example

Target Market(s)

Potential clients that need Attorney services.

Industry/Entity Type

Law Firm

Contact Information for Business Card

We would like the front and back to be two different colors. Current business cards are teal front, grey back and are a vertical design. We are open to options with colors.

Font styles to use
Serif

Colors
33a6d7
33b8a4
b9b9b9
5c5c5c

Requirements
Must have
• Logo supplied needs to go on the card and stationary.
• Match website color palate, www.vernac-law.example
• Be professional and not too wordy.
• Criminal Law, Civil Litigation, Personal Injury, Restraining Orders need to be on the card.
Nice to have
• RELATIONSHIPS. RESPECT. RESULTS. on the back of the card.
Should not have
• Not be too busy/wordy or too flashy.

```html
<!DOCTYPE html>
<html lang="en">
<head>
<meta charset="utf-8">
<title>Vernac Law Letterhead</title>
<link rel="stylesheet" href="https://fonts.googleapis.com/css2?family=Source+Sans+3:wght@400;600&display=swap">
<style>
  :root {
    --backdrop: #cdcdcd;
    --paper: #ededed;
    --teal: #1b7f8c;
    --ink: #565656;
    --ink-dark: #1e1e1e;
    --band: #4a4a4a;
    --band-light: #5e5e5e;
    --footer-text: #f2f2f2;
  }
  * { margin: 0; padding: 0; box-sizing: border-box; }
  html, body { width: 1200px; height: 1193px; overflow: hidden; background: var(--backdrop); }
  body { font-family: "Source Sans 3", sans-serif; color: var(--ink); }

  .letterhead {
    position: absolute; left: 163px; top: 30px;
    width: 874px; height: 1133px;
    background: var(--paper);
    overflow: hidden;
  }

  .firm-name {
    position: absolute; left: 79px; top: 200px; width: 240px;
    text-align: center;
    font-size: 34px; font-weight: 400; letter-spacing: 2px;
    text-transform: uppercase; color: var(--teal);
  }

  .contact-block {
    position: absolute; top: 112px; left: 462px;
    display: flex; font-size: 15px; line-height: 20px; color: #333;
  }
  .address { display: flex; padding-right: 12px; border-right: 1px solid var(--teal); }
  .address svg { margin: 22px 6px 0 0; flex: none; }
  .reach { padding-left: 12px; }
  .reach-line { display: flex; align-items: center; gap: 6px; }
  .reach-line svg { flex: none; }

  .letter { position: absolute; left: 79px; top: 335px; width: 725px; font-size: 15.5px; }
  .date { margin-bottom: 12px; }
  .recipient { line-height: 22px; }
  .recipient .to { margin-bottom: 3px; }
  .salutation { margin-top: 44px; margin-bottom: 18px; }
  .body-text p { line-height: 21px; text-indent: 7px; margin-bottom: 20px; }

  .signature-mark {
    width: 150px; height: 50px; margin-top: 8px;
    background: linear-gradient(90deg, #d9d9d9, #e6e6e6);
    border-radius: 4px;
  }
  .signer { margin-top: 10px; margin-left: 3px; font-size: 18px; font-weight: 600; color: var(--ink-dark); }

  .footer { position: absolute; left: 0; bottom: 0; width: 874px; height: 50px; }
  .footer svg { position: absolute; inset: 0; }
  .practice-areas {
    position: absolute; left: 463px; top: 12px;
    font-size: 17.5px; color: var(--footer-text); white-space: nowrap;
  }
  .practice-areas .dot { font-size: 10px; vertical-align: 2px; margin: 0 3px; }
</style>
</head>
<body>
<main class="letterhead">
  <div class="firm-name">Vernac Law</div>

  <div class="contact-block">
    <div class="address">
      <svg width="12" height="16" viewBox="0 0 12 16"><path d="M6 0a6 6 0 0 0-6 6c0 4.5 6 10 6 10s6-5.5 6-10a6 6 0 0 0-6-6zm0 8.5a2.5 2.5 0 1 1 0-5 2.5 2.5 0 0 1 0 5z" fill="var(--teal)"/></svg>
      <div>Southern California,<br>4700 Harbor View Ave.<br>#210</div>
    </div>
    <div class="reach">
      <div class="reach-line">
        <svg width="13" height="13" viewBox="0 0 24 24"><path d="M6.6 10.8a15 15 0 0 0 6.6 6.6l2.2-2.2a1 1 0 0 1 1-.25 11.4 11.4 0 0 0 3.6.57 1 1 0 0 1 1 1V20a1 1 0 0 1-1 1A17 17 0 0 1 3 4a1 1 0 0 1 1-1h3.5a1 1 0 0 1 1 1c0 1.25.2 2.45.57 3.57a1 1 0 0 1-.25 1z" fill="var(--teal)"/></svg>
        <span>(555) 014-2290</span>
      </div>
      <div class="reach-line">
        <svg width="13" height="10" viewBox="0 0 13 10"><rect width="13" height="10" rx="1" fill="var(--teal)"/><path d="M0.5 1l6 4.5 6-4.5" stroke="var(--paper)" stroke-width="1.2" fill="none"/></svg>
        <span>office@vernac-law.example</span>
      </div>
      <div class="reach-line">
        <svg width="13" height="13" viewBox="0 0 13 13"><circle cx="6.5" cy="6.5" r="6.5" fill="var(--teal)"/><path d="M1 6.5h11M6.5 1c-2.5 3-2.5 8 0 11M6.5 1c2.5 3 2.5 8 0 11" stroke="var(--paper)" stroke-width="1" fill="none"/></svg>
        <span>www.vernac-law.example</span>
      </div>
    </div>
  </div>

  <section class="letter">
    <p class="date">December 24, 2015,</p>
    <div class="recipient">
      <p class="to">To: Alan Mercer</p>
      <p>Northwind Group</p>
      <p>City,State,Zip</p>
    </div>
    <p class="salutation">Dear Mr Mercer.</p>
    <div class="body-text">
      <p>Lorem ipsum dolor sit amet, consectetur adipisicing elit, sed do eiusmod carte incididunt ut labore et dolore magna aliqua. Ut enim ad minim veniam, quis exercitation ullamco laboris nisi ut aliquip ex ea commodo consequat. review dolor in reprehenderit in voluptate .</p>
      <p>build voluptas sit aspernatur aut odit aut fugit, sed quia consequunture fugite ratione voluptatem equi nesciunt. Neque porro quisquam est, qui dolor ipsum sit amet, consectetur, adipisci velit, sed quia non numquam eius modilos iduim labore et dolore .</p>
      <p>Excepteur sint occaecat cupidatat non proident, sunt in culpa qui officia deser accusantium dolore mque laudantium, totam rem aperiam, eaque ipsa quae an ratione voluptatem sequi nesciunt. Nequ porro quisquam est, qui dolorem ie anim id est laborum. Sed ut perspiciatis unde omnis iste natus error sit volupte accusantium doloremque laudantium, totam rem aperiam, eaque ipsa quae ab verit atis et quasi architecto beatae vitae .</p>
      <p>Fuia voluptas sit aspernatur aut odit aut fugit, sed quia consequuntur magni ratione voluptatem seq ui nesciunt. Neque porro quisquam est, qui dolorem eps sit amet, consectetur, adipisci velit, sed quia non numquam eius modi tempora labore et dolore .</p>
    </div>
    <div class="signature-mark" role="img" aria-label="Handwritten signature"></div>
    <p class="signer">Daniel Reyes</p>
  </section>

  <footer class="footer">
    <svg width="874" height="50" viewBox="0 0 874 50">
      <polygon points="0,34 874,34 874,50 0,50" fill="var(--band-light)"/>
      <polygon points="0,17 432,17 420,30 0,30" fill="var(--teal)"/>
      <polygon points="456,0 874,0 874,50 410,50 410,34 422,34" fill="var(--band)"/>
    </svg>
    <p class="practice-areas"><span class="dot">◆</span>Criminal Law <span class="dot">◆</span>Civil Litigation <span class="dot">◆</span>Personal Injury</p>
  </footer>
</main>
</body>
</html>
```